Velvette by Marisa Dunn business cards

I am after a business card that will fit the name of my business - velvette.
I want something classy and sexy and nothing tacky.
Ideas that I like are Zebra print backgrounds glitter back grounds
Two ideas I had were
1. Zebra print in black and white, the name Velvette by Marisa Dunn and a shilouette of a woman laying on top of the name. Or instead of zebra a glitter background.
2. Idea very similar except for instead of a woman a pair of lips maybe a hot pink glitter or a gold glitter depending on background with the business name between the lips.
Or you can do something completely different.

```html
<!DOCTYPE html>
<html lang="en">
<head>
<meta charset="utf-8">
<title>Velvette by Marisa Dunn — Business Cards</title>
<link rel="stylesheet" href="https://fonts.googleapis.com/css2?family=Josefin+Sans:wght@300;400;700&display=swap">
<style>
  :root {
    --backdrop: #e9e7e4;
    --card-dark: #2f2c2c;
    --card-mid: #4a4646;
    --card-light: #5c5757;
    --ink-light: #f1f0ee;
    --ink-soft: #d9d6d3;
    --icon: #bdb9b5;
    --shadow: rgba(0, 0, 0, 0.28);
  }
  * { box-sizing: border-box; margin: 0; padding: 0; }
  html, body {
    width: 1200px;
    height: 873px;
    overflow: hidden;
    background: var(--backdrop);
    font-family: "Josefin Sans", "Century Gothic", sans-serif;
  }
  .sheet {
    width: 1200px;
    height: 873px;
    display: flex;
    align-items: center;
    justify-content: center;
    gap: 50px;
  }
  .card {
    position: relative;
    width: 525px;
    height: 300px;
    border-radius: 4px;
    overflow: hidden;
    box-shadow: 0 14px 30px var(--shadow);
    color: var(--ink-light);
  }
  .card-texture {
    position: absolute;
    inset: 0;
  }
  .card--front .card-texture {
    background: linear-gradient(135deg, var(--card-dark) 0%, var(--card-light) 50%, var(--card-dark) 100%);
  }
  .card--back .card-texture {
    background: radial-gradient(ellipse at 55% 50%, var(--card-light) 0%, var(--card-mid) 40%, var(--card-dark) 100%);
  }

  /* Front: brand name */
  .brand {
    position: absolute;
    inset: 0;
    display: flex;
    flex-direction: column;
    align-items: center;
    justify-content: center;
    font-weight: 300;
    color: var(--ink-light);
  }
  .brand-name {
    font-size: 74px;
    letter-spacing: 2px;
    line-height: 1;
    text-transform: uppercase;
  }
  .brand-owner {
    margin-top: 14px;
    font-size: 26px;
    letter-spacing: 1px;
  }

  /* Back: contact details */
  .contact {
    position: absolute;
    left: 70px;
    top: 42px;
    display: grid;
    grid-template-columns: 34px auto;
    column-gap: 18px;
    align-items: center;
  }
  .contact-name {
    grid-column: 2;
    font-weight: 700;
    font-size: 27px;
    line-height: 1.05;
  }
  .contact-role {
    grid-column: 2;
    font-weight: 300;
    font-size: 19px;
    margin-bottom: 22px;
    color: var(--ink-soft);
  }
  .contact-icon {
    grid-column: 1;
    width: 22px;
    height: 22px;
    justify-self: center;
  }
  .contact-line {
    grid-column: 2;
    font-weight: 300;
    font-size: 18px;
    line-height: 1.45;
    color: var(--ink-soft);
  }
  .contact-icon svg {
    width: 22px;
    height: 22px;
    fill: none;
    stroke: var(--icon);
    stroke-width: 1.4;
    stroke-linejoin: round;
    stroke-linecap: round;
  }
</style>
</head>
<body>
<main class="sheet">

  <section class="card card--front" aria-label="Business card front">
    <div class="card-texture" role="img" aria-label="Soft grey zebra stripe print background"></div>
    <div class="brand">
      <span class="brand-name">Velvette</span>
      <span class="brand-owner">by Marisa Dunn</span>
    </div>
  </section>

  <section class="card card--back" aria-label="Business card back">
    <div class="card-texture" role="img" aria-label="Faint zebra stripe print on dark grey background"></div>
    <div class="contact">
      <span class="contact-name">Marisa Dunn</span>
      <span class="contact-role">Proprietor</span>

      <span class="contact-icon" style="grid-row: span 2;">
        <svg viewBox="0 0 22 22" aria-hidden="true"><path d="M3 11 L11 4 L19 11"/><path d="M5.5 9.5 V18 H16.5 V9.5"/><rect x="9" y="13" width="4" height="5"/></svg>
      </span>
      <span class="contact-line">17, Marlowe Ave</span>
      <span class="contact-line">Glendale, CA 91204</span>

      <span class="contact-icon">
        <svg viewBox="0 0 22 22" aria-hidden="true"><path d="M6 3 H9 L10.5 7 L8.5 8.5 C9.5 10.8 11.2 12.5 13.5 13.5 L15 11.5 L19 13 V16 C19 17.5 17.5 19 16 19 C9 18.5 3.5 13 3 6 C3 4.5 4.5 3 6 3 Z"/></svg>
      </span>
      <span class="contact-line">310 555 0147</span>

      <span class="contact-icon">
        <svg viewBox="0 0 22 22" aria-hidden="true"><rect x="6.5" y="2.5" width="9" height="17" rx="1.5"/><path d="M6.5 5.5 H15.5 M6.5 16 H15.5"/></svg>
      </span>
      <span class="contact-line">310 555 0193</span>

      <span class="contact-icon">
        <svg viewBox="0 0 22 22" aria-hidden="true"><rect x="3" y="5.5" width="16" height="11"/><path d="M3 5.5 L11 12 L19 5.5"/></svg>
      </span>
      <span class="contact-line">velvettebymd@velvettebymd.com</span>
    </div>
  </section>

</main>
</body>
</html>
```